Tollen Ridge Canvas Camps

I am Moving from nest QiV and Qelt to host my own website to create direct bookings. I haves booking platform, I just need a website to embed it into. I want a catchy website to attract potential guests to book at my accommodation located near morvane national park in Alberta, Canada.

Here is my nest QiV links:
https://www.nestqiv.ca/rooms/2048613927465105319?viralityEntryPoint=1&s=76

https://www.nestqiv.ca/rooms/2093547718260493127?viralityEntryPoint=1&s=76

https://www.nestqiv.ca/rooms/2184736590218374662?viralityEntryPoint=1&s=76

https://www.nestqiv.ca/rooms/2065128834710952483?viralityEntryPoint=1&s=76

https://www.nestqiv.ca/rooms/2317465098321857704?viralityEntryPoint=1&s=76

```html
<!DOCTYPE html>
<html lang="en">
<head>
<meta charset="utf-8">
<title>Tollen Ridge Canvas Camps</title>
<link href="https://fonts.googleapis.com/css2?family=Raleway:wght@600;700;800&family=Roboto:wght@400;500;700&display=swap" rel="stylesheet">
<style>
:root{
  --pink:#c8104f;
  --navy:#161b57;
  --navy-deep:#10143f;
  --ink:#1b1b1b;
  --body:#555;
  --muted:#8a8a8a;
  --gold:#d4a72c;
  --line:#d9d9d9;
  --white:#fff;
}
*{box-sizing:border-box;margin:0;padding:0}
html,body{width:1200px;height:4910px;overflow:hidden}
body{position:relative;background:var(--white);font-family:'Roboto',sans-serif;color:var(--ink)}
.abs{position:absolute}
.btn{position:absolute;background:var(--pink);color:var(--white);border-radius:30px;font:700 13px 'Roboto',sans-serif;text-transform:uppercase;display:flex;align-items:center;justify-content:center;letter-spacing:.2px}
.brand{display:flex;align-items:center;gap:12px;font-family:'Raleway',sans-serif;font-weight:800;text-transform:uppercase;line-height:1.1}
.brand-dot{border-radius:50%;flex:none}
.section-title{position:absolute;left:0;width:1200px;text-align:center;font:700 44px 'Raleway',sans-serif;color:var(--ink);letter-spacing:-.5px}
.section-title span{color:var(--pink)}
.section-title::after{content:"";display:block;width:96px;height:3px;background:var(--ink);margin:14px auto 0}

/* hero */
.hero{left:0;top:0;width:1200px;height:790px;background:linear-gradient(180deg,#6d7378 0%,#3e4640 35%,#26302a 65%,#1f2621 100%)}
.hero .brand{position:absolute;left:143px;top:60px;color:var(--white);font-size:19px;width:240px}
.menu-btn{left:1006px;top:80px;width:48px;height:48px;border-radius:50%;background:var(--white);display:flex;flex-direction:column;align-items:center;justify-content:center;gap:4px}
.menu-btn i{display:block;width:18px;height:2.5px;background:#333;border-radius:2px}
.hero-title{left:0;top:252px;width:1200px;text-align:center;font:800 50px/67px 'Raleway',sans-serif;color:var(--white);text-transform:uppercase;text-shadow:0 3px 8px rgba(0,0,0,.55);letter-spacing:-.5px}
.hero-title mark{background:var(--pink);color:var(--white);padding:0 8px}
.mouse{left:589px;top:532px;width:22px;height:34px;border:2px solid var(--white);border-radius:12px}
.mouse::after{content:"";position:absolute;left:8px;top:6px;width:2px;height:7px;background:var(--white);border-radius:2px}
.search{left:145px;top:625px;width:912px;height:124px;background:var(--white);border-radius:10px;box-shadow:0 8px 24px rgba(0,0,0,.15);z-index:3}
.search h3{position:absolute;left:22px;top:26px;font:500 17px 'Roboto',sans-serif;color:#222}
.field{position:absolute;top:56px;height:44px;border:1px solid var(--line);border-radius:3px;font-size:11.5px;color:#333;display:flex;align-items:center;justify-content:space-between;padding:0 14px 0 18px}
.field b{width:8px;height:8px;background:#999;border-radius:1px}
.search .btn{left:743px;top:56px;width:142px;height:44px;font-size:13px}

/* about */
.about-art{left:105px;top:872px;width:463px;height:362px;border-radius:232px 232px 0 0;background:radial-gradient(circle at 50% 70%,#5a5a5a 0%,#2a2222 55%,#140f0f 100%)}
.about-title{left:632px;top:862px;font:700 44px 'Raleway',sans-serif;letter-spacing:-.5px}
.about-title span{color:var(--pink)}
.about-rule{left:632px;top:923px;width:190px;height:3px;background:var(--ink)}
.about-text{left:632px;top:958px;width:424px;font-size:14px;line-height:28.3px;color:var(--body);text-align:justify}

/* featured */
.featured-bg{left:0;top:1320px;width:1200px;height:1020px;background:linear-gradient(180deg,#fff 0%,#ececee 20%,#e4e5e8 55%,#f5f5f7 85%,#fff 100%)}
.card{position:absolute;width:261px;height:372px;background:var(--white);border:1px solid #ddd;border-radius:4px;box-shadow:0 6px 18px rgba(0,0,0,.12);overflow:hidden}
.card .photo{height:200px}
.card h4{position:absolute;left:28px;top:218px;width:210px;font:700 15.5px/22px 'Roboto',sans-serif;text-transform:uppercase;color:#222}
.card .meta{position:absolute;left:28px;font-size:13px;color:#333;display:flex;align-items:center;gap:8px}
.card .meta.red{color:var(--pink)}
.card .meta i{width:11px;height:11px;border:2px solid #222;border-radius:50%;display:block}
.card .meta s{width:12px;height:10px;background:#222;display:block;border-radius:1px}
.card .meta u{font-weight:700;text-decoration:none}
.card .btn{left:140px;width:110px;height:38px;font-size:11px}
.arrow{width:44px;height:44px;border-radius:50%;border:2px solid #777;background:rgba(255,255,255,.6);display:flex;align-items:center;justify-content:center}
.dots{display:flex;gap:14px}
.dots i{width:8px;height:8px;border-radius:50%;background:#c7c7c7;display:block}
.dots i.on{background:var(--pink)}

/* testimonials */
.testi-bg{left:0;top:2440px;width:1200px;height:400px;background:linear-gradient(180deg,#fff 0%,#eef0f2 40%,#dfe3e6 100%)}
.testi{position:absolute;top:2476px;width:330px;display:flex;gap:18px}
.avatar{width:68px;height:68px;border-radius:50%;border:3px solid #ddd;background:linear-gradient(135deg,#c9b3a5,#7c6a62);flex:none}
.testi p{font-size:11.5px;line-height:18.5px;color:#888;text-align:justify}
.testi .who{font-size:11.5px;font-weight:700;color:#222;margin-top:14px;text-transform:uppercase}
.testi .stars{color:var(--gold);font-size:17px;letter-spacing:3px;margin-top:6px}

/* gallery */
.tile{position:absolute;height:305px}
.play{left:272px;top:3282px;width:54px;height:54px;border-radius:50%;background:var(--pink);display:flex;align-items:center;justify-content:center}

/* blog */
.post-photo{position:absolute;top:3715px;width:419px;height:362px}
.post-body{position:absolute;top:4028px;width:376px;background:var(--white);border-top:5px solid var(--pink);padding:20px 0 0 24px;height:90px}
.post-body h4{font:700 18px 'Roboto',sans-serif;text-transform:uppercase;color:#222}
.post-meta{position:absolute;top:4078px;font-size:11px;color:#222;display:flex;gap:8px;align-items:center}
.post-meta i{width:10px;height:10px;border:2px solid var(--pink);display:block;border-radius:2px}
.post-text{position:absolute;top:4105px;width:316px;font-size:13px;line-height:23px;color:#777;text-align:justify}

/* footer */
.footer{left:0;top:4340px;width:1200px;height:570px;background:linear-gradient(180deg,var(--navy) 0%,var(--navy-deep) 100%)}
.footer .brand{position:absolute;left:143px;top:4620px;color:var(--white);font-size:24px;width:300px}
.foot-h{position:absolute;top:4538px;font:700 18px 'Roboto',sans-serif;color:var(--white);text-transform:uppercase}
.foot-links{left:488px;top:4596px;list-style:none;color:var(--white);font-size:14px;line-height:27.5px}
.news-input{left:703px;top:4602px;width:234px;height:34px;background:var(--white);font-size:12px;color:#666;display:flex;align-items:center;padding-left:14px}
.news-btn{left:937px;top:4602px;width:95px;height:34px;background:var(--pink);color:var(--white);font:700 13px 'Roboto',sans-serif;display:flex;align-items:center;justify-content:center}
.news-note{left:703px;top:4655px;font-size:15px;color:var(--white)}
.socials{left:703px;top:4700px;display:flex;gap:10px}
.socials i{width:31px;height:31px;border-radius:50%;background:var(--white);display:block}
.socials i.on{background:var(--pink)}
.foot-rule{left:132px;top:4797px;width:936px;height:1px;background:rgba(255,255,255,.2)}
.copyright{left:0;top:4844px;width:1200px;text-align:center;font-size:13px;color:var(--white)}
.chat{left:1055px;top:4340px;width:66px;height:66px;border-radius:50%;background:var(--pink);border:3px solid var(--white);display:flex;align-items:center;justify-content:center;z-index:4}
</style>
</head>
<body>

<!-- HERO -->
<section class="abs hero" role="img" aria-label="Geodesic glamping dome among tall evergreen trees under a grey sky, with a small cabin at right"></section>
<div class="hero">
  <div class="brand"><span class="brand-dot" style="width:34px;height:34px;border:3px solid #fff"></span>Tollen Ridge Canvas Camps</div>
</div>
<div class="abs menu-btn"><i></i><i></i><i></i></div>
<h1 class="abs hero-title">Experience Morvane's Beauty<br>From the Comfort of<br><mark>Your Own Cabin</mark></h1>
<div class="abs mouse"></div>
<svg class="abs" style="left:595px;top:566px" width="10" height="8" viewBox="0 0 10 8"><path d="M1 1l4 5 4-5" stroke="#fff" stroke-width="1.5" fill="none"/></svg>
<svg class="abs" style="left:0;top:690px" width="1200" height="110" viewBox="0 0 1200 110">
  <path d="M0 100 Q600 0 1200 100 L1200 110 L0 110Z" fill="#fff"/>
  <path d="M0 92 Q600 -4 1200 92" stroke="#161b57" stroke-width="7" fill="none"/>
  <path d="M0 100 Q600 6 1200 100" stroke="#fff" stroke-width="3" fill="none"/>
</svg>

<div class="abs search">
  <h3>Find Your Cabin</h3>
  <div class="field" style="left:25px;width:192px">Location or Properties<b style="border-radius:50%"></b></div>
  <div class="field" style="left:227px;width:163px">Check in<b></b></div>
  <div class="field" style="left:400px;width:163px">Check Out<b></b></div>
  <div class="field" style="left:571px;width:163px">Number of Guests<b style="width:5px"></b></div>
  <div class="btn">Book Now</div>
</div>

<!-- ABOUT -->
<div class="abs about-art" role="img" aria-label="Illustration of mountains, pines and a glamping dome inside a circular emblem"></div>
<div class="abs" style="left:100px;top:1234px;width:20px;height:2px;background:#555"></div>
<div class="abs" style="left:318px;top:1234px;width:180px;height:2px;background:#555"></div>
<h2 class="abs about-title">ABOUT <span>US</span></h2>
<div class="abs about-rule"></div>
<p class="abs about-text">Sed ut perspiciatis unde omnis iste natus error sit voluptatem accusantium doloremque laudantium, totam rem aperiam, eaque ipsa quae ab illo inventore veritatis et quasi architecto beatae vitae dicta sunt explicabo. Nemo enim ipsam voluptatem quia voluptas sit aspernatur aut odit aut fugit, sed quia consequuntur magni dolores eos qui ratione voluptatem sequi nesciunt. Neque porro quisquam est, qui dolorem ipsum quia dolor sit amet, consectetur, adipisci velit, sed quia non numquam eius modi tempora incidunt ut labore et dolore magnam aliquam quaerat voluptatem.</p>
<div class="btn" style="left:632px;top:1268px;width:145px;height:42px">Read More</div>

<!-- FEATURED -->
<div class="abs featured-bg" role="img" aria-label="Faint misty forest backdrop"></div>
<h2 class="section-title" style="top:1455px">FEATURED <span>LISTINGS</span></h2>

<div class="card" style="left:175px;top:1619px">
  <div class="photo" role="img" aria-label="Glowing dome under a twilight sky among dark pines" style="background:linear-gradient(180deg,#2d3f62 0%,#526588 55%,#141a22 100%)"></div>
  <h4>#2 Dome - Tollen Ridge Canvas Camps</h4>
  <div class="meta red" style="top:276px"><i style="border-color:#c8104f"></i>Up to 24 hrs</div>
  <div class="meta" style="top:308px"><s></s>3,000 sq ft</div>
  <div class="meta" style="top:337px"><u>$</u>Up to $500</div>
  <div class="btn" style="top:322px">Book Now</div>
</div>
<div class="card" style="left:469px;top:1695px;z-index:2">
  <div class="photo" role="img" aria-label="Dome lit at night beneath green and purple northern lights" style="background:linear-gradient(180deg,#4a3c78 0%,#3f8a6a 45%,#1a1e1c 80%,#4a3018 100%)"></div>
  <h4>#3 Dome - Tollen Ridge Canvas Camps</h4>
  <div class="meta red" style="top:276px"><i style="border-color:#c8104f"></i>Up to 24 hrs</div>
  <div class="meta" style="top:308px"><s></s>3,000 sq ft</div>
  <div class="meta" style="top:337px"><u>$</u>Up to $500</div>
  <div class="btn" style="top:322px">Book Now</div>
</div>
<div class="card" style="left:762px;top:1619px">
  <div class="photo" role="img" aria-label="White dome with red deck chairs among spruce trees" style="background:linear-gradient(180deg,#8fa1ad 0%,#53684a 45%,#cfd3d6 75%,#6b4a3c 100%)"></div>
  <h4>#4 Dome - Tollen Ridge Canvas Camps</h4>
  <div class="meta red" style="top:276px"><i style="border-color:#c8104f"></i>Up to 24 hrs</div>
  <div class="meta" style="top:308px"><s></s>3,000 sq ft</div>
  <div class="meta" style="top:337px"><u>$</u>Up to $500</div>
  <div class="btn" style="top:322px">Book Now</div>
</div>
<div class="abs arrow" style="left:104px;top:1821px"><svg width="12" height="16" viewBox="0 0 12 16"><path d="M9 2L3 8l6 6" stroke="#555" stroke-width="2" fill="none"/></svg></div>
<div class="abs arrow" style="left:1051px;top:1821px"><svg width="12" height="16" viewBox="0 0 12 16"><path d="M3 2l6 6-6 6" stroke="#555" stroke-width="2" fill="none"/></svg></div>
<div class="abs dots" style="left:551px;top:2120px"><i class="on"></i><i></i><i></i><i></i><i></i></div>

<!-- TESTIMONIALS -->
<div class="abs testi-bg" role="img" aria-label="Faint mountain landscape backdrop"></div>
<h2 class="section-title" style="top:2328px">GUEST <span>TESTIMONIALS</span></h2>
<div class="testi" style="left:128px">
  <div class="avatar" role="img" aria-label="Guest portrait"></div>
  <div><p>fantastic stay. loved the fact we had a private bathroom. the hosts parents both stopped over to make sure we had everything we needed. Chaos (the dog) made"</p>
  <div class="who">— Maren Holt</div><div class="stars">★★★★☆</div></div>
</div>
<div class="testi" style="left:460px">
  <div class="avatar" role="img" aria-label="Guest portrait" style="background:linear-gradient(135deg,#bbb,#555)"></div>
  <div><p>"Very enjoyable stay, the glampsite is very well run, they give you everything you need to enjoy your stay. The only issue we ran into was the lack"</p>
  <div class="who">— Maren Holt</div><div class="stars">★★★★★</div></div>
</div>
<div class="testi" style="left:782px">
  <div class="avatar" role="img" aria-label="Guest portrait" style="background:linear-gradient(135deg,#d2c8c0,#8a7d74)"></div>
  <div><p>"Great experience made all the better for Aldo's local knowledge on the moon's path and possible northern lights sightings"</p>
  <div class="who">— Corbin Lyle</div><div class="stars">★★★★☆</div></div>
</div>
<div class="abs arrow" style="left:67px;top:2528px;width:34px;height:34px;border-width:1.5px"><svg width="10" height="12" viewBox="0 0 10 12"><path d="M7 1L2 6l5 5" stroke="#777" stroke-width="1.5" fill="none"/></svg></div>
<div class="abs arrow" style="left:1099px;top:2528px;width:34px;height:34px;border-width:1.5px"><svg width="10" height="12" viewBox="0 0 10 12"><path d="M3 1l5 5-5 5" stroke="#777" stroke-width="1.5" fill="none"/></svg></div>
<div class="btn" style="left:488px;top:2694px;width:224px;height:42px">View More Reviews</div>

<!-- GALLERY -->
<div class="tile" style="left:0;top:2842px;width:296px;background:linear-gradient(180deg,#cbb99a,#7c8a6a 50%,#8a6a4c)" role="img" aria-label="Dome interior with chairs facing a valley view"></div>
<div class="tile" style="left:302px;top:2842px;width:296px;background:linear-gradient(180deg,#a9bccc,#4f6a45 50%,#7a6650)" role="img" aria-label="Red deck chairs on a wooden deck overlooking hills"></div>
<div class="tile" style="left:602px;top:2842px;width:296px;background:linear-gradient(180deg,#cfc0a4,#97a6a8 45%,#6a5444)" role="img" aria-label="Dome interior with window view of forest"></div>
<div class="tile" style="left:904px;top:2842px;width:296px;background:linear-gradient(180deg,#3c4c66,#9aa0a6 50%,#c8c8c8)" role="img" aria-label="Small bathroom with window and sink"></div>
<div class="tile" style="left:0;top:3155px;width:598px;background:linear-gradient(180deg,#6f93bd,#a5b7c4 30%,#2c4a30 60%,#2d6d8c 85%,#1c4250)" role="img" aria-label="Mountain lake with a small forested island"></div>
<div class="tile" style="left:602px;top:3155px;width:296px;background:linear-gradient(180deg,#65708a,#a9b8cc 50%,#e4eaf2)" role="img" aria-label="Dome in winter snow"></div>
<div class="tile" style="left:904px;top:3155px;width:296px;background:linear-gradient(180deg,#b8c0c6,#6f7a60 45%,#8a6c4a)" role="img" aria-label="Wooden deck beside a cabin"></div>
<div class="abs play"><svg width="18" height="20" viewBox="0 0 18 20"><path d="M3 2l13 8-13 8z" fill="#fff"/></svg></div>

<!-- BLOG -->
<h2 class="section-title" style="top:3568px">BLOG <span>POSTS</span></h2>
<div class="post-photo" style="left:152px;background:linear-gradient(180deg,#0e1422,#2a3040 40%,#8a8e94 65%,#1a1c22)" role="img" aria-label="Lit dome at night"></div>
<div class="post-photo" style="left:629px;background:linear-gradient(180deg,#d8cdb7,#a89a82 45%,#5a4a3e 80%)" role="img" aria-label="Dome interior with bed and rug"></div>
<div class="post-body" style="left:172px"><h4>Quis Nostrud Exercitatio</h4></div>
<div class="post-body" style="left:649px"><h4>Quis Nostrud Exercitatio</h4></div>
<div class="post-meta" style="left:204px"><i></i>January 20,2025 | <i style="border-radius:50%"></i>Admin</div>
<div class="post-meta" style="left:681px"><i></i>January 20,2025 | <i style="border-radius:50%"></i>Admin</div>
<p class="post-text" style="left:204px">Lorem ipsum dolor sit amet, consectetur adipiscing elit, sed do eiusmod tempor incididunt ut labore et dolore magna aliquis ipsum suspendisse ultices gravidasus</p>
<p class="post-text" style="left:681px">Lorem ipsum dolor sit amet, consectetur adipiscing elit, sed do eiusmod tempor incididunt ut labore et dolore magna aliquis ipsum suspendisse ultices gravidasus</p>
<div class="btn" style="left:204px;top:4225px;width:154px;height:42px;box-shadow:0 6px 16px rgba(200,16,79,.35)">Read More</div>
<div class="btn" style="left:681px;top:4225px;width:154px;height:42px">Read More</div>
<div class="abs dots" style="left:562px;top:4313px"><i class="on"></i><i></i><i></i><i></i></div>

<!-- FOOTER -->
<div class="abs footer" role="img" aria-label="Faint night forest backdrop"></div>
<svg class="abs" style="left:0;top:4335px" width="1200" height="110" viewBox="0 0 1200 110">
  <path d="M0 0 L1200 0 L1200 8 Q600 120 0 8Z" fill="#fff"/>
  <path d="M0 14 Q600 124 1200 14" stroke="#fff" stroke-width="3" fill="none"/>
</svg>
<div class="abs chat"><svg width="30" height="26" viewBox="0 0 30 26"><path d="M3 2h24v16H12l-6 6v-6H3z" fill="#fff"/><circle cx="10" cy="10" r="2" fill="#c8104f"/><circle cx="15" cy="10" r="2" fill="#c8104f"/><circle cx="20" cy="10" r="2" fill="#c8104f"/></svg></div>
<div class="footer-brand"><div class="brand" style="position:absolute;left:143px;top:4628px;color:#fff;font-size:24px;width:310px"><span class="brand-dot" style="width:40px;height:40px;border:3px solid #fff"></span>Tollen Ridge Canvas Camps</div></div>
<div class="foot-h" style="left:488px">Quick Links</div>
<ul class="abs foot-links"><li>About us</li><li>Properties</li><li>Owner Login</li><li>List with Us</li><li>Contact Us</li></ul>
<div class="foot-h" style="left:703px">Sign up Newsletter</div>
<div class="abs news-input">Enter Email</div>
<div class="abs news-btn">SIGN UP</div>
<div class="abs news-note">Keep up to date as we expand in to new regions</div>
<div class="abs socials" aria-label="Social links"><i></i><i class="on"></i><i></i><i></i></div>
<div class="abs foot-rule"></div>
<div class="abs copyright">Copyright © 2026 Companyname. All rights reserved &nbsp;|&nbsp; Privacy policy &nbsp;|&nbsp; Terms and conditions</div>

</body>
</html>
```